Dalvick's Business Card

I need some designs for a new business card including the new logo attached. An old example of our business card is also attached to show all the data that should be included on the new design.
**I added some more examples someone had mocked up**

Contact Information for Business Card

Should include all info on other examples uploaded.

```html
<!DOCTYPE html>
<html lang="en">
<head>
<meta charset="utf-8">
<title>Dalvick's Business Card</title>
<link href="https://fonts.googleapis.com/css2?family=Montserrat:wght@400;500;700;800&display=swap" rel="stylesheet">
<style>
  :root {
    --brand-blue: #1769b8;
    --brand-red: #e2262b;
    --card-dark: #2a2b2d;
    --card-white: #ffffff;
    --ink: #1d1d1f;
    --backdrop: #d9dadc;
  }
  * { box-sizing: border-box; margin: 0; padding: 0; }
  html, body { width: 1200px; height: 1026px; overflow: hidden; }
  body {
    background: var(--backdrop);
    font-family: "Montserrat", sans-serif;
    position: relative;
  }
  .card {
    position: absolute;
    left: 210px;
    width: 780px;
    height: 446px;
    overflow: hidden;
    box-shadow: 0 10px 28px rgba(0,0,0,0.22);
  }
  /* Back side */
  .card-back { top: 40px; background: var(--card-dark); }
  .card-back .edge-stripe {
    position: absolute; left: 0; right: 0; bottom: 0; height: 12px;
    background: var(--brand-blue);
    border-top: 3px solid var(--brand-red);
  }
  .card-back .brand {
    position: absolute; right: 48px; bottom: 62px; text-align: left;
  }
  .brand-name {
    font-weight: 800; color: var(--brand-blue); letter-spacing: 1px; line-height: 1;
  }
  .brand-tagline {
    font-weight: 700; color: var(--brand-red); text-transform: uppercase; letter-spacing: 0.3px;
  }
  .card-back .brand-name { font-size: 50px; }
  .card-back .brand-tagline { font-size: 13px; margin-top: 4px; }

  /* Front side */
  .card-front { top: 540px; background: var(--card-white); }
  .card-front .brand {
    position: absolute; left: 50px; top: 46px; display: flex; align-items: center; gap: 16px;
  }
  .brand-dot {
    width: 58px; height: 58px; border-radius: 50%; background: var(--brand-blue); flex: none;
  }
  .card-front .brand-name { font-size: 58px; }
  .card-front .brand-tagline { font-size: 15px; margin-top: 4px; }

  .contact { position: absolute; left: 54px; top: 170px; }
  .person-name { font-size: 27px; font-weight: 800; color: var(--brand-blue); }
  .contact-rule {
    position: absolute; left: 54px; top: 212px; width: 640px; height: 2px; background: var(--brand-blue);
  }
  .contact-list { position: absolute; left: 54px; top: 226px; list-style: none; }
  .contact-list li {
    display: flex; align-items: center; gap: 12px;
    font-size: 17px; font-weight: 500; color: var(--ink); margin-bottom: 7px;
  }
  .contact-list svg { width: 16px; height: 16px; flex: none; }
  .credential {
    position: absolute; right: 86px; top: 318px;
    font-size: 18px; font-weight: 500; color: var(--ink); letter-spacing: 0.5px;
  }
  .footer-bands { position: absolute; left: 0; top: 0; width: 780px; height: 446px; }
  .footer-note {
    position: absolute; right: 40px; bottom: 16px;
    font-size: 18px; font-weight: 500; color: var(--card-white); letter-spacing: 0.8px;
  }
</style>
</head>
<body>

  <section class="card card-back" aria-label="Card back">
    <div class="brand">
      <div class="brand-name">DALVICK'S</div>
      <div class="brand-tagline">Air Conditioning &amp; Heating Service</div>
    </div>
    <div class="edge-stripe"></div>
  </section>

  <section class="card card-front" aria-label="Card front">
    <svg class="footer-bands" viewBox="0 0 780 446" aria-hidden="true">
      <path d="M0 342 L440 356 L440 360 L0 346 Z" fill="var(--brand-blue)"/>
      <path d="M0 352 L450 364 Q470 365 478 382 L0 382 Z" fill="var(--brand-red)"/>
      <path d="M0 396 L470 396 Q482 378 505 378 L780 378 L780 446 L0 446 Z" fill="var(--brand-blue)"/>
    </svg>

    <div class="brand">
      <span class="brand-dot"></span>
      <div>
        <div class="brand-name">DALVICK'S</div>
        <div class="brand-tagline">Air Conditioning &amp; Heating Service</div>
      </div>
    </div>

    <div class="contact">
      <div class="person-name">Mark Dalvick</div>
    </div>
    <div class="contact-rule"></div>
    <ul class="contact-list">
      <li>
        <svg viewBox="0 0 16 16"><path d="M3 1.5h3l1.2 3.3-1.8 1.2a8 8 0 0 0 4.6 4.6l1.2-1.8 3.3 1.2v3a1.5 1.5 0 0 1-1.6 1.5C7 14 2 9 1.5 3.1A1.5 1.5 0 0 1 3 1.5z" fill="var(--brand-red)"/></svg>
        555.014.2277
      </li>
      <li>
        <svg viewBox="0 0 16 16"><rect x="1" y="3" width="14" height="10" rx="1" fill="var(--brand-blue)"/><path d="M1.5 3.8 8 9l6.5-5.2" stroke="#fff" stroke-width="1.3" fill="none"/></svg>
        hvacdalvick@mailbox.com
      </li>
    </ul>

    <div class="credential">LICENSED &amp; INSURED</div>
    <div class="footer-note">FAMILY OWNED &amp; OPERATED</div>
  </section>

</body>
</html>
```